The Brookhaven Sessions - Concert Series Website Design

I've recently decided to launch a concert series in my living room and would love a website to use to promote the series. I'm looking for a simple Wix design that I could take over once it's complete. I'll provide the logo for which I'd like the website to utilize the color scheme.

Target Market(s)

Music lovers in Denver

Industry/Entity Type

Music

Coding

Coded - Design and coding required

Number of Pages Required

2 page

Font styles to use
Script

Requirements
Must have
• 2 pages - one for concert goers to see the schedule and rsvp, and one for artists about the booking process

```html
<!DOCTYPE html>
<html lang="en">
<head>
<meta charset="utf-8">
<title>The Brookhaven Sessions</title>
<link href="https://fonts.googleapis.com/css2?family=Marcellus&family=Inter:wght@400;500;600&display=swap" rel="stylesheet">
<style>
  :root {
    --ink: #2e0a45;
    --plum: #7a2355;
    --gold: #fdc651;
    --accent: #f0a24a;
    --cream: #fdf5e4;
    --peach: #fde2a8;
    --text: #3a3340;
    --white: #ffffff;
  }
  * { box-sizing: border-box; margin: 0; padding: 0; }
  html, body { width: 1200px; height: 3129px; overflow: hidden; }
  body { font-family: "Inter", Arial, sans-serif; color: var(--text); background: var(--white); position: relative; }
  .display { font-family: "Marcellus", Georgia, serif; font-weight: 400; }
  .btn { display: flex; align-items: center; justify-content: center; border-radius: 24px; font-weight: 600; font-size: 15px; position: absolute; }
  .btn-gold { background: var(--gold); color: var(--ink); }
  .btn-plum { background: var(--plum); color: var(--gold); }

  /* header */
  .site-header { position: absolute; top: 0; left: 0; width: 1200px; height: 86px; background: var(--white); }
  .brand { position: absolute; left: 112px; top: 16px; display: flex; align-items: center; gap: 12px; }
  .brand-dot { width: 40px; height: 40px; border-radius: 50%; background: var(--plum); }
  .brand-name { font-family: "Marcellus", Georgia, serif; font-size: 21px; line-height: 22px; color: var(--plum); width: 150px; text-transform: uppercase; }
  .nav { position: absolute; left: 757px; top: 35px; display: flex; gap: 16px; font-size: 15px; color: var(--ink); }
  .header-cta { left: 887px; top: 22px; width: 200px; height: 45px; }

  /* hero */
  .hero { position: absolute; top: 86px; left: 0; width: 1200px; height: 600px; text-align: center; color: var(--white); }
  .hero-photo { position: absolute; inset: 0; background: linear-gradient(180deg, #7a4a6a 0%, #5a2a78 40%, #3d0f5c 75%, #2e0a45 100%); }
  .hero-kicker { position: absolute; top: 296px; width: 100%; font-size: 24px; letter-spacing: 2px; }
  .hero-title { position: absolute; top: 330px; width: 100%; font-size: 52px; letter-spacing: 2px; }
  .hero-sub { position: absolute; top: 404px; width: 100%; font-size: 15px; }
  .hero .btn { top: 462px; height: 45px; }

  /* about */
  .about { position: absolute; top: 686px; left: 0; width: 1200px; height: 632px; }
  .about-panel { position: absolute; left: 0; top: 0; width: 601px; height: 632px; background: var(--plum); }
  .about-photo { position: absolute; left: 115px; top: 107px; width: 370px; height: 417px; background: linear-gradient(160deg, #5a3a2a, #2a1a18 60%, #3b4a3a); }
  .about-copy { position: absolute; left: 683px; top: 128px; width: 404px; }
  .section-title { font-size: 44px; line-height: 43px; color: var(--ink); letter-spacing: 1px; }
  .rule { width: 55px; height: 4px; background: var(--accent); margin-top: 14px; }
  .about-copy p { font-size: 15px; line-height: 24px; text-align: justify; margin-top: 12px; }
  .about-copy p.first { margin-top: 30px; }
  .about-copy .em { color: var(--plum); font-weight: 600; }
  .about-copy p.last { margin-top: 20px; }

  /* sessions */
  .sessions { position: absolute; top: 1318px; left: 0; width: 1200px; height: 798px; }
  .sessions-head { position: absolute; top: 126px; width: 100%; text-align: center; }
  .sessions-head .rule, .reserve-head .rule { margin: 16px auto 0; }
  .cards { position: absolute; top: 265px; left: 112px; display: flex; gap: 23px; }
  .card { width: 227px; height: 418px; background: var(--cream); position: relative; text-align: center; }
  .card-photo { height: 171px; position: relative; }
  .badge { position: absolute; left: 8px; top: 8px; background: var(--plum); color: var(--white); font-size: 11px; font-weight: 500; padding: 4px 8px 4px 8px; }
  .badge::before { content: ""; display: inline-block; width: 4px; height: 4px; border-radius: 50%; background: var(--white); margin-right: 7px; vertical-align: middle; }
  .card-name { font-size: 25px; color: var(--ink); margin-top: 18px; }
  .card-genre { font-size: 13px; margin-top: 4px; }
  .card-divider { height: 1px; background: #eadfc8; margin-top: 16px; }
  .card-meta { font-size: 13.5px; line-height: 20px; margin-top: 14px; }
  .card .btn { left: 20px; top: 351px; width: 187px; height: 45px; }

  /* reserve */
  .reserve { position: absolute; top: 2116px; left: 0; width: 1200px; height: 852px; background: var(--peach); }
  .reserve-head { position: absolute; top: 103px; width: 100%; text-align: center; }
  .reserve-intro { position: absolute; top: 200px; width: 100%; text-align: center; font-size: 15px; line-height: 24px; }
  .reserve-intro .em { color: var(--plum); font-weight: 600; }
  .reserve-form { position: absolute; left: 225px; top: 281px; width: 750px; height: 455px; background: var(--cream); }
  .field { position: absolute; height: 37px; border-bottom: 1px solid #b7a99a; font-size: 15px; color: var(--ink); }
  .field.select::after { content: ""; position: absolute; right: 12px; top: 6px; width: 7px; height: 7px; border-right: 1.5px solid var(--ink); border-bottom: 1.5px solid var(--ink); transform: rotate(45deg); }
  .reserve-form .btn { left: 280px; top: 364px; width: 190px; height: 45px; }

  /* footer */
  .site-footer { position: absolute; top: 2968px; left: 0; width: 1200px; height: 161px; background: var(--ink); }
  .site-footer .brand { top: 60px; }
  .site-footer .brand-name { color: var(--cream); }
  .copyright { position: absolute; right: 110px; top: 73px; font-size: 15px; color: var(--white); }
</style>
</head>
<body>
  <header class="site-header">
    <div class="brand"><span class="brand-dot"></span><span class="brand-name">The Brookhaven Sessions</span></div>
    <nav class="nav"><span>Home</span><span>Music</span></nav>
    <span class="btn btn-gold header-cta">Confirm Attendance</span>
  </header>

  <section class="hero">
    <div class="hero-photo" role="img" aria-label="Crowd dancing at a lively concert under purple lights"></div>
    <p class="hero-kicker display">LIVE • INTIMATE • DENVER</p>
    <h1 class="hero-title display">THE BROOKHAVEN SESSIONS</h1>
    <p class="hero-sub">An intimate concert series in the heart of Denver — where music meets connection.</p>
    <span class="btn btn-gold" style="left:430px;width:187px;">Upcoming Shows</span>
    <span class="btn btn-plum" style="left:634px;width:135px;">RSVP Now</span>
  </section>

  <section class="about">
    <div class="about-panel"></div>
    <div class="about-photo" role="img" aria-label="Singer with acoustic guitar performing at a microphone with a band behind"></div>
    <div class="about-copy">
      <h2 class="section-title display">WHERE MUSIC<br>FEELS PERSONAL</h2>
      <div class="rule" style="margin-top:16px"></div>
      <p class="first">The Brookhaven Sessions is a curated living room concert experience in Denver.<br>We bring together emerging and established artists for stripped-down, immersive performances in an intimate setting.</p>
      <p>No big stages. No crowded venues.<br><span class="em">Just powerful music and meaningful connection.</span></p>
      <p class="last">Every show is limited-capacity to preserve the atmosphere — so when you’re here, you’re part of something special.</p>
    </div>
  </section>

  <section class="sessions">
    <div class="sessions-head">
      <h2 class="section-title display">UPCOMING SESSIONS</h2>
      <div class="rule"></div>
    </div>
    <div class="cards">
      <article class="card">
        <div class="card-photo" role="img" aria-label="Singer performing under blue stage light" style="background:linear-gradient(150deg,#6a2a9a,#2a2a7a 55%,#1a1a3a)"><span class="badge">Limited Seating Available</span></div>
        <h3 class="card-name display">Jhon k</h3>
        <p class="card-genre">Genre: Acoustic</p>
        <div class="card-divider"></div>
        <p class="card-meta">March 28, 2026<br>7:00 PM<br>(address shared after RSVP)</p>
        <span class="btn btn-gold">RSVP Now!</span>
      </article>
      <article class="card">
        <div class="card-photo" role="img" aria-label="Smiling singer with headphones at a studio microphone" style="background:linear-gradient(150deg,#3a3a3a,#6a5a4a 60%,#2a2a2a)"><span class="badge">Limited Seating Available</span></div>
        <h3 class="card-name display">James</h3>
        <p class="card-genre">Genre: Acoustic</p>
        <div class="card-divider"></div>
        <p class="card-meta">March 29, 2026<br>7:00 PM<br>(address shared after RSVP)</p>
        <span class="btn btn-gold">RSVP Now!</span>
      </article>
      <article class="card">
        <div class="card-photo" role="img" aria-label="Two singers performing together with microphones" style="background:linear-gradient(150deg,#4a4a4a,#8a7a6a 55%,#3a3a3a)"><span class="badge">Limited Seating Available</span></div>
        <h3 class="card-name display">Harry</h3>
        <p class="card-genre">Genre: Acoustic</p>
        <div class="card-divider"></div>
        <p class="card-meta">April 10, 2026<br>7:00 PM<br>(address shared after RSVP)</p>
        <span class="btn btn-gold">RSVP Now!</span>
      </article>
      <article class="card">
        <div class="card-photo" role="img" aria-label="Singer with acoustic guitar and band on a small stage" style="background:linear-gradient(150deg,#5a3a2a,#2a1a18 60%,#3b4a3a)"><span class="badge">Limited Seating Available</span></div>
        <h3 class="card-name display">Jane</h3>
        <p class="card-genre">Genre: Acoustic</p>
        <div class="card-divider"></div>
        <p class="card-meta">April 22, 2026<br>7:00 PM<br>(address shared after RSVP)</p>
        <span class="btn btn-gold">RSVP Now!</span>
      </article>
    </div>
  </section>

  <section class="reserve">
    <div class="reserve-head">
      <h2 class="section-title display">RESERVE YOUR SEAT</h2>
      <div class="rule"></div>
    </div>
    <p class="reserve-intro">Seats are intentionally limited to preserve the intimacy of<br>each session. <span class="em">RSVP early to guarantee your spot.</span></p>
    <form class="reserve-form">
      <div class="field" style="left:53px;top:45px;width:303px;">Name</div>
      <div class="field" style="left:393px;top:45px;width:303px;">Email</div>
      <div class="field select" style="left:53px;top:133px;width:303px;">Select Show</div>
      <div class="field" style="left:393px;top:133px;width:303px;">Guest Count</div>
      <div class="field" style="left:53px;top:218px;width:643px;height:122px;">Message</div>
      <span class="btn btn-plum">Reserve Your Seat</span>
    </form>
  </section>

  <footer class="site-footer">
    <div class="brand"><span class="brand-dot"></span><span class="brand-name">The Brookhaven Sessions</span></div>
    <p class="copyright">2026 The Brookhaven Sessions. All Rights Reserved.</p>
  </footer>
</body>
</html>
```